Velvet Lantern rebranding my business with a new business card

I have my new logo and now I need a refresher on my business cards. I really want something fun and fresh. I like black background or anything to make the color pop.
Logo
Name: Velvet Lantern
Contact Info as stated below:
Mira Pellow
555-013-4762
Logo
Name: Velvet Lantern
Mira Pellow
555-013-4762
fb.me/VelvetLanternbyMira
Instagram: @VelvetLanternbyMira

Industry/Entity Type

Business

Contact Information for Business Card

double-sided. Logo on one side. Contact info on the other.

Requirements
Must have
• Logo
• Name: Velvet Lantern
• Contact Info as stated below:
• Mira Pellow
• 555-013-4762
• fb.me/VelvetLanternbyMira
• fb.me/VelvetLanternbyMira

```html
<!DOCTYPE html>
<html lang="en">
<head>
<meta charset="utf-8">
<title>Velvet Lantern — Business Cards</title>
<link rel="stylesheet" href="https://fonts.googleapis.com/css2?family=Open+Sans:wght@400;600&display=swap">
<style>
  :root {
    --backdrop: #c8c8ca;
    --card-black: #1c1819;
    --card-shade: #141112;
    --icing-pink: #e395b8;
    --icing-deep: #b5718f;
    --soft-pink: #f0b2cd;
    --ink-white: #ffffff;
  }
  * { margin: 0; padding: 0; box-sizing: border-box; }
  html, body { width: 1200px; height: 973px; overflow: hidden; }
  body {
    background: var(--backdrop);
    font-family: "Open Sans", sans-serif;
    position: relative;
  }
  .card {
    position: absolute;
    width: 512px;
    height: 297px;
    background: radial-gradient(circle at 50% 55%, var(--card-black), var(--card-shade));
    overflow: hidden;
    box-shadow: 0 2px 8px rgba(0,0,0,0.25);
  }
  .card--front { left: 110px; top: 19px; }
  .card--back-drip { left: 243px; top: 339px; }
  .card--back-plain { left: 110px; top: 653px; }

  .icing-band {
    position: absolute;
    left: 0; top: 0;
    width: 100%;
    height: 72px;
    background: linear-gradient(to bottom, var(--icing-pink) 0%, var(--icing-pink) 45%, var(--icing-deep) 75%, var(--card-black) 100%);
  }

  .brand-name {
    position: absolute;
    left: 0; width: 100%;
    top: 80px;
    text-align: center;
    color: var(--icing-pink);
    font-size: 37px;
    font-weight: 400;
    line-height: 44px;
    letter-spacing: 1px;
  }
  .role {
    position: absolute;
    left: 0; width: 100%;
    top: 125px;
    text-align: center;
    color: var(--ink-white);
    font-size: 13px;
  }
  .contact {
    position: absolute;
    left: 178px;
    top: 172px;
    color: var(--ink-white);
  }
  .contact__name { font-size: 25px; line-height: 32px; }
  .contact__phone { font-size: 25px; line-height: 32px; }
  .contact__social {
    display: inline-flex;
    align-items: center;
    gap: 5px;
    margin-top: 14px;
    margin-left: -16px;
    padding: 0 10px 0 3px;
    border: 2px solid var(--icing-pink);
    border-radius: 12px;
    color: var(--soft-pink);
    font-size: 13px;
    line-height: 20px;
  }
  .contact__social-dot {
    width: 14px; height: 14px;
    border-radius: 50%;
    background: var(--icing-pink);
  }

  .emblem {
    position: absolute;
    width: 196px; height: 196px;
    border: 4px solid var(--icing-pink);
    border-radius: 50%;
    display: flex;
    align-items: center;
    justify-content: center;
    text-align: center;
    color: var(--icing-pink);
    font-size: 26px;
    font-weight: 600;
    line-height: 1.15;
  }
  .card--back-drip .emblem { left: 177px; top: 96px; }
  .card--back-plain .emblem { left: 167px; top: 31px; }
</style>
</head>
<body>

  <section class="card card--front" aria-label="Business card front">
    <div class="icing-band" role="img" aria-label="Pink dripping icing border along the top edge"></div>
    <h1 class="brand-name">Velvet Lantern</h1>
    <p class="role">Managing Director</p>
    <div class="contact">
      <p class="contact__name">Mira Pellow</p>
      <p class="contact__phone">555-013-4762</p>
      <p class="contact__social"><span class="contact__social-dot"></span>fb.me/VelvetLanternbyMira</p>
    </div>
  </section>

  <section class="card card--back-drip" aria-label="Business card back with icing border">
    <div class="icing-band" role="img" aria-label="Pink dripping icing border along the top edge"></div>
    <div class="emblem">Velvet<br>Lantern</div>
  </section>

  <section class="card card--back-plain" aria-label="Business card back">
    <div class="emblem">Velvet<br>Lantern</div>
  </section>

</body>
</html>
```